National online rug retailer needs a home page design

See the FloorNest logo and create a home page design around that color theme. Details are spelled out in word document uploaded below.

Apparently this website did not take my attachement showing the logo and basic requirements.  If you would send me your email address, I will send you the attachment directly.
Best regards,
Tom Vance
tvance@mrdcorp.example

Target Market(s)

The target market is home owners 25 to 75 years old with combined incomes over $100,000 per year.

Industry/Entity Type

Online

Requirements
Must have
• Lots of white space with black letters and creative use of red and possibly one other color. Would like a compelling call to action button.

```html
<!DOCTYPE html>
<html lang="en">
<head>
<meta charset="utf-8">
<title>FloorNest.com – Home</title>
<link href="https://fonts.googleapis.com/css2?family=Open+Sans:wght@400;600;700&display=swap" rel="stylesheet">
<style>
:root{
  --red:#d10a0a;
  --ink:#1d1d1d;
  --muted:#555;
  --line:#e4e4e4;
  --page:#efefef;
  --footer:#f4f4f4;
  --dark:#3a3a3a;
  --nav:#1a1a1a;
}
*{margin:0;padding:0;box-sizing:border-box}
html,body{width:878px;height:1200px;overflow:hidden}
body{font-family:"Open Sans",Arial,sans-serif;color:var(--ink);background:#fff;position:relative}
a{color:inherit;text-decoration:none}
.abs{position:absolute}

/* header */
.logo{left:74px;top:24px;display:flex;flex-direction:column}
.logo-row{display:flex;align-items:center;gap:6px}
.logo-mark{width:26px;height:26px;background:var(--red)}
.logo-name{font-size:27px;font-weight:400;color:var(--ink);letter-spacing:-.5px}
.logo-tag{font-size:8px;color:var(--muted);margin-left:64px;margin-top:2px}
.search{left:298px;top:32px;width:294px;height:34px;border:2px solid #e2e2e2;display:flex}
.search span{flex:1;font-size:9px;font-style:italic;color:#aaa;padding:10px 8px}
.search-btn{width:36px;height:34px;margin:-2px -2px 0 0;background:#4a4a4a;display:flex;align-items:center;justify-content:center}
.util{right:74px;top:21px;font-size:8.5px;color:#444;text-align:right}
.util .count{background:#333;color:#fff;padding:0 3px}
.phone{right:74px;top:40px;font-size:13px;font-weight:700;color:var(--red)}
.account{right:74px;top:64px;font-size:8.5px;color:#444;display:flex;gap:6px;align-items:center}
.account .chat{background:#555;color:#fff;padding:2px 4px}
.account .online{font-weight:700;color:#333;display:flex;align-items:center;gap:3px}

/* nav */
.nav{left:0;top:98px;width:878px;height:29px;background:var(--nav)}
.nav ul{list-style:none;display:flex;margin-left:74px;width:731px;height:29px}
.nav li{flex:1;color:#fff;font-size:11px;font-weight:600;display:flex;align-items:center;justify-content:center;border-right:1px solid #333}
.nav li.active{background:var(--red);border:1px solid #ff4a4a}

.page-bg{left:0;top:127px;width:878px;height:851px;background:var(--page)}

/* hero */
.hero{left:74px;top:135px;width:731px;height:271px;background:linear-gradient(180deg,#8e4a2c 0%,#b9742f 30%,#e8dcc8 55%,#c83a1f 85%,#a42614 100%)}
.hero-title{left:20px;bottom:8px;font-size:23px;font-weight:700;line-height:25px;color:var(--ink)}
.hero-title em{font-style:normal;color:var(--red)}

/* content */
.content{left:74px;top:414px;width:731px;height:556px;background:#fff}
.section-title{left:12px;top:12px;font-size:15px;font-weight:700}
.section-title em{font-style:normal;color:var(--red)}
.title-rule{left:14px;top:38px;width:602px;height:1px;background:var(--line)}
.grid{left:14px;top:49px;display:grid;grid-template-columns:repeat(4,120px);column-gap:16px;row-gap:16px}
.card{width:120px;height:154px;border:1px solid var(--line);padding:9px 9px 0}
.card .thumb{width:100px;height:114px}
.card .meta{display:flex;justify-content:space-between;align-items:center;margin-top:9px;font-size:9.5px}
.card .name{color:var(--red)}
.card .add{font-weight:700;font-size:8.5px}

.browse{left:560px;top:9px;width:156px}
.browse-head{background:linear-gradient(#3a3a3a,#111);color:#fff;font-size:13.5px;font-weight:700;padding:5px 11px;height:29px}
.browse ul{list-style:none}
.browse li{height:32px;border-bottom:1px solid var(--line);display:flex;justify-content:space-between;align-items:center;padding:0 3px 0 10px;font-size:9.5px;font-weight:700;color:#333}
.browse li span{font-weight:400;font-size:8px}
.like-head{left:560px;top:304px;width:156px;height:29px;background:var(--red);border:1px solid #a00;color:#fff;font-size:13.5px;font-weight:700;padding:4px 10px}
.like-img{left:560px;top:342px;width:156px;height:198px;background:linear-gradient(160deg,#7a2a1c,#c7a270 45%,#e4cf9f 70%,#8c4a2a)}

/* footer */
.footer{left:0;top:978px;width:878px;height:180px;background:var(--footer)}
.fcol{top:20px}
.fcol h4{font-size:11px;color:var(--red);font-weight:700;margin-bottom:4px}
.fcol li{list-style:none;font-size:8.5px;color:#444;line-height:13.2px}
.pay{left:573px;top:86px;display:flex;gap:4px;align-items:center}
.pay i{display:block;width:24px;height:15px;background:#c9cfd8;border-radius:2px}
.pay b{display:block;width:90px;height:20px;background:#dfe5ee;margin-left:6px;border-radius:2px}
.badges{left:572px;top:119px;display:flex;gap:5px;align-items:center}
.badges .seal{width:34px;height:34px;border-radius:50%;background:#e2c24a}
.badges .tag{width:46px;height:20px;background:#d7d7d7;border-radius:2px}
.bottom{left:0;top:1158px;width:878px;height:42px;background:var(--dark);color:#ddd;font-size:9px;padding:14px 94px}
</style>
</head>
<body>

<header>
  <div class="abs logo">
    <div class="logo-row"><span class="logo-mark"></span><span class="logo-name">FloorNest.com</span></div>
    <span class="logo-tag">for domestic and heirloom values</span>
  </div>
  <div class="abs search"><span>Enter your search here...</span>
    <div class="search-btn"><svg width="14" height="14" viewBox="0 0 14 14"><circle cx="6" cy="6" r="4.3" fill="none" stroke="#fff" stroke-width="2"/><line x1="9.2" y1="9.2" x2="13" y2="13" stroke="#fff" stroke-width="2"/></svg></div>
  </div>
  <div class="abs util">Items: <span class="count">0</span> &nbsp;|&nbsp; Total $0.00 &nbsp;|&nbsp; View Cart &nbsp;|&nbsp; Checkout</div>
  <div class="abs phone">Order toll-free: 1-800-555-0147</div>
  <div class="abs account"><span>My Account</span>|<span>Sign In</span><span class="chat">Live Chat</span>
    <span class="online"><svg width="9" height="9" viewBox="0 0 9 9"><circle cx="4.5" cy="2.5" r="2.2" fill="#d10a0a"/><path d="M0.5 9a4 3.5 0 0 1 8 0z" fill="#d10a0a"/></svg>Online</span></div>
</header>

<nav class="abs nav"><ul>
  <li class="active">Home</li><li>Selection guides</li><li>Rug Care</li><li>FAQ</li><li>Return Policy</li><li>Free Shipping</li><li>Clearance Rugs</li>
</ul></nav>

<div class="abs page-bg"></div>

<section class="abs hero" role="img" aria-label="Close-up photo of stacked shag and woven rugs in cream, brown and red">
  <h1 class="abs hero-title"><em>For</em> Domestic<br>and Heirloom <em>values</em></h1>
</section>

<main class="abs content">
  <h2 class="abs section-title"><em>Fuatured</em> Rugs</h2>
  <div class="abs title-rule"></div>
  <div class="abs grid">
    <div class="card"><div class="thumb" role="img" aria-label="Persian rug photo" style="background:linear-gradient(135deg,#8a3a14,#c88a3a,#5a2a10)"></div><div class="meta"><span class="name">Persian Rugs</span><span class="add">Add +</span></div></div>
    <div class="card"><div class="thumb" role="img" aria-label="Modern circle-pattern rug photo" style="background:linear-gradient(135deg,#3a2418,#4a3020,#c8a060)"></div><div class="meta"><span class="name">Modern Rugs</span><span class="add">Add +</span></div></div>
    <div class="card"><div class="thumb" role="img" aria-label="Ziegler rug in a room photo" style="background:linear-gradient(180deg,#b59a80,#d8d2c4,#c9a27a)"></div><div class="meta"><span class="name">Ziegler Rugs</span><span class="add">Add +</span></div></div>
    <div class="card"><div class="thumb" role="img" aria-label="Oriental rug under dining table photo" style="background:linear-gradient(180deg,#a08a6a,#6a3a24,#8a2a1a)"></div><div class="meta"><span class="name">Oriental Rugs</span><span class="add">Add +</span></div></div>

    <div class="card"><div class="thumb" role="img" aria-label="Kilim rug in bedroom photo" style="background:linear-gradient(180deg,#c9b090,#8a4a34,#5a2a1c)"></div><div class="meta"><span class="name">kilim Rugs</span><span class="add">Add +</span></div></div>
    <div class="card"><div class="thumb" role="img" aria-label="Shag rug in living room photo" style="background:linear-gradient(180deg,#c8c0b4,#b8504a,#ddd6cc)"></div><div class="meta"><span class="name">Shag Rugs</span><span class="add">Add +</span></div></div>
    <div class="card"><div class="thumb" role="img" aria-label="Ziegler rug in a room photo" style="background:linear-gradient(180deg,#b59a80,#d8d2c4,#c9a27a)"></div><div class="meta"><span class="name">Ziegler Rugs</span><span class="add">Add +</span></div></div>
    <div class="card"><div class="thumb" role="img" aria-label="Tribal rug in hallway photo" style="background:linear-gradient(135deg,#b0a080,#7a2a1a,#2a2a3a)"></div><div class="meta"><span class="name">Tribal Rugs</span><span class="add">Add +</span></div></div>

    <div class="card"><div class="thumb" role="img" aria-label="Clearance rug with armchair photo" style="background:linear-gradient(180deg,#6a5a3a,#8a7a5a,#7a5a3a)"></div><div class="meta"><span class="name">Clearance Rugs</span><span class="add">Add +</span></div></div>
    <div class="card"><div class="thumb" role="img" aria-label="Moroccan runner rug photo" style="background:linear-gradient(180deg,#8a6a4a,#b82a1a,#8a6a4a)"></div><div class="meta"><span class="name">Moroccan Rugs</span><span class="add">Add +</span></div></div>
    <div class="card"><div class="thumb" role="img" aria-label="Modern circle-pattern rug photo" style="background:linear-gradient(135deg,#3a2418,#4a3020,#c8a060)"></div><div class="meta"><span class="name">Modern Rugs</span><span class="add">Add +</span></div></div>
    <div class="card"><div class="thumb" role="img" aria-label="Ziegler rug in a room photo" style="background:linear-gradient(180deg,#b59a80,#d8d2c4,#c9a27a)"></div><div class="meta"><span class="name">Ziegler Rugs</span><span class="add">Add +</span></div></div>
  </div>

  <aside class="abs browse">
    <div class="browse-head">Browse</div>
    <ul>
      <li>RUG THEME<span>+</span></li><li>COLOR WAY<span>+</span></li><li>SIZE<span>+</span></li><li>SHAPE<span>+</span></li>
      <li>FIBER CONTENT<span>+</span></li><li>MFGR. BRAND<span>+</span></li><li>MFGR.COLLECTION<span>+</span></li><li>PRICE<span>+</span></li>
    </ul>
  </aside>
  <div class="abs like-head">You may also like</div>
  <div class="abs like-img" role="img" aria-label="Photo of rolled ornate traditional rugs"></div>
</main>

<footer class="abs footer">
  <div class="abs fcol" style="left:94px"><h4>Customer Service</h4><ul>
    <li>Shipping</li><li>Return Policy</li><li>Privacy Policy</li><li>Ordering &amp; Delivery</li><li>Checklist</li><li>Terms of Use</li><li>Terms of Sale</li><li>Contact Us</li><li>Environmental Policy</li></ul></div>
  <div class="abs fcol" style="left:286px"><h4>Resources</h4><ul>
    <li>Product Articles</li><li>Learning Center</li><li>Help</li><li>Refer A Friend</li><li>FloorNest Blog</li><li>Room Scene Viewer</li><li>Site Map</li><li>FAQ</li><li>Customer Testimonials</li><li>Photo Gallery</li></ul></div>
  <div class="abs fcol" style="left:470px"><h4>Corporate Info</h4><ul>
    <li>About FloorNest.com</li><li>Careers</li><li>Affiliates</li></ul></div>
  <div class="abs pay" aria-label="Accepted payment methods"><i></i><i></i><i></i><i></i><i></i><b></b></div>
  <div class="abs badges" aria-label="Security and trust badges"><span class="seal"></span><span class="seal"></span><span class="tag"></span><span class="tag"></span><span class="tag"></span></div>
</footer>
<div class="abs bottom">© Copyrights 2013 All rights Reserved</div>

</body>
</html>
```